Gestaltung Mini Katalog für bayerische Polomarke
Gestaltung "Mini" Katalog für bayerische Polomarke
Zielgruppe
Unsere Marke richtet sich an den klassischen Lifestyle Kunden. 20 - 45 Jahre alt, legt Wert auf das Äussere und Kleidung.... Mag es gerne besonders, modern und chic.
Hallo,
wir planen derzeit einen kleinen Katalog von 8-10 Seiten im Format DIN A5 (kein Muss). Präsentiert wird darin die erste bayerische Polomarke K&M reitmode und die aktuellen Kollektionen an Polo-Teamshirts.
Die Fotos dazu werden in den nächsten 14 Tagen entstehen.
Wir suchen nun jemanden, der uns das ganze in eine moderne Gestaltung bringt. Für Vorschläge bitte statt der Fotos alternative Fotos einsetzen.
Unsere Marke bewegt sich im mittleren Preissegment und präsentiert eine ganz besondere Sportart. All das muss in dem Katalog rüber kommen. Neben den Produkt- und Modefotos werden klassische Polobilder integriert, um das Gefühl diesen Sports mit zu vermitteln.
Die Grundfarben sollten sich an denen von K&M reitmode orientieren: schwarz, blau, weiss.... Wobei wir für andere Farben, wenn diese passen bzw. begründet sind auch interessiert sind.

```html
<!DOCTYPE html>
<html lang="de">
<head>
<meta charset="utf-8">
<title>K&amp;M reitmode – Katalog Rückseite</title>
<link rel="stylesheet" href="https://fonts.googleapis.com/css2?family=Didact+Gothic&display=swap">
<style>
  :root {
    --ink: #000000;
    --rim: #5a9cc2;
    --rim-deep: #1f4a66;
    --rim-shadow: #0a1a26;
    --brand: #dcdcdc;
    --text: #ffffff;
  }
  html, body {
    margin: 0;
    padding: 0;
    overflow: hidden;
    background: var(--ink);
  }
  .cover {
    position: relative;
    width: 1200px;
    height: 1200px;
    background: var(--ink);
    overflow: hidden;
    font-family: "Didact Gothic", "Century Gothic", sans-serif;
    color: var(--text);
  }
  .horizon {
    position: absolute;
    inset: 0;
  }
  .brand {
    position: absolute;
    left: 0;
    right: 0;
    top: 440px;
    text-align: center;
    color: var(--brand);
    font-weight: 400;
  }
  .brand-mark {
    display: block;
    font-size: 120px;
    line-height: 1;
    letter-spacing: 4px;
  }
  .brand-line {
    display: block;
    margin-top: 58px;
    font-size: 30px;
    letter-spacing: 1px;
  }
  .contact {
    position: absolute;
    top: 1005px;
    left: 0;
    right: 0;
    font-size: 26px;
    line-height: 36px;
  }
  .contact-col {
    position: absolute;
    top: 0;
    margin: 0;
    font-style: normal;
    white-space: nowrap;
  }
  .contact-address { left: 180px; }
  .contact-phone { left: 480px; }
  .contact-web { left: 805px; }
</style>
</head>
<body>
  <main class="cover">
    <svg class="horizon" width="1200" height="1200" viewBox="0 0 1200 1200" aria-hidden="true">
      <defs>
        <radialGradient id="planet-glow" cx="600" cy="-52" r="802" gradientUnits="userSpaceOnUse">
          <stop offset="0" stop-color="#000000"/>
          <stop offset="0.6" stop-color="#000000"/>
          <stop offset="0.85" stop-color="var(--rim-shadow)"/>
          <stop offset="0.96" stop-color="var(--rim-deep)"/>
          <stop offset="1" stop-color="var(--rim)"/>
        </radialGradient>
      </defs>
      <circle cx="600" cy="-52" r="802" fill="url(#planet-glow)"/>
    </svg>

    <div class="brand">
      <span class="brand-mark">K&amp;M</span>
      <span class="brand-line">reitmode</span>
    </div>

    <footer class="contact">
      <address class="contact-col contact-address">Beispielhaus AG<br>Reiterweg 12<br>81234 Beispielstadt</address>
      <p class="contact-col contact-phone">TEL : 0821 / 704418<br>FAX : 0821 / 704419<br>MAIL : info@beispielhaus.de</p>
      <p class="contact-col contact-web">INTERNET :<br>www.beispielhaus.de</p>
    </footer>
  </main>
</body>
</html>
```